Brimlow Plumbing Solutions

This is for my new plumbing company, I have attached an example of what I’m going for but want it to look better.

Target Market(s)

Home owners, real estate, etc.

Industry/Entity Type

Plumbing

Font styles to use
Other font styles liked:
• As per my logo and other examples uploaded

Colors

Designer to choose colors to be used in the design.

Requirements
Must have
• Must include my logo provided and similar to my flyer I have attached but better

```html
<!DOCTYPE html>
<html lang="en">
<head>
<meta charset="UTF-8">
<title>Brimlow Plumbing Solutions – Flyer</title>
<link href="https://fonts.googleapis.com/css2?family=Poppins:wght@400;500;600;700&display=swap" rel="stylesheet">
<style>
  :root {
    --navy: #262a6b;
    --sky: #47a6dc;
    --orange: #f5961f;
    --white: #ffffff;
    --ink: #2b2b3a;
    --backdrop: #d3d4d5;
    --tile: #e3eef8;
  }
  * { box-sizing: border-box; margin: 0; padding: 0; }
  html, body { width: 1200px; height: 1200px; overflow: hidden; }
  body {
    background: var(--backdrop);
    font-family: "Poppins", Arial, sans-serif;
    position: relative;
  }
  .flyer {
    position: absolute;
    left: 244px; top: 72px;
    width: 712px; height: 1056px;
    background: var(--white);
    overflow: hidden;
  }
  .header-wave { position: absolute; left: 0; top: 0; width: 712px; height: 380px; }
  .brand {
    position: absolute; top: 70px; left: 0; width: 100%;
    text-align: center; color: var(--white);
    font-weight: 600; font-size: 30px; letter-spacing: 0.5px;
  }
  .tagline {
    position: absolute; top: 184px; left: 0; width: 100%;
    text-align: center; color: var(--white);
    font-weight: 400; font-size: 19px; line-height: 30px;
  }
  .offer-badge {
    position: absolute; left: 71px; top: 326px;
    width: 222px; height: 222px; border-radius: 50%;
    background: var(--navy); border: 6px solid var(--sky);
    display: flex; flex-direction: column; align-items: center; justify-content: center;
    color: var(--white); text-align: center; font-size: 16px; line-height: 22px;
  }
  .offer-badge .discount {
    color: var(--orange); font-weight: 600; font-size: 31px; line-height: 40px;
  }
  .services-title {
    position: absolute; left: 70px; top: 578px;
    color: var(--navy); font-weight: 600; font-size: 36px;
  }
  .service {
    position: absolute; width: 160px; margin-left: -80px;
    text-align: center; color: var(--ink); font-size: 16px; line-height: 20px;
  }
  .service-icon {
    display: block; width: 52px; height: 52px; margin: 0 auto 12px;
    border-radius: 10px; background: var(--tile);
  }
  .contact-bar {
    position: absolute; left: 0; bottom: 0; width: 100%; height: 102px;
    background: var(--sky);
    display: flex; align-items: center; justify-content: space-between;
    padding: 0 40px 0 46px; color: var(--white); font-size: 13px;
  }
  .contact-item { display: flex; align-items: center; gap: 8px; }
  .contact-item.phone { font-size: 16px; font-weight: 500; }
  .contact-icon { width: 24px; height: 24px; flex: none; }
</style>
</head>
<body>
  <main class="flyer">
    <svg class="header-wave" viewBox="0 0 712 380" aria-hidden="true">
      <path d="M0 0 H712 V342 C600 380 520 320 420 300 C300 276 180 310 0 328 Z" fill="var(--sky)"/>
      <path d="M0 0 H712 V328 C610 360 520 304 420 286 C300 262 180 296 0 314 Z" fill="var(--navy)"/>
      <circle cx="506" cy="346" r="21" fill="var(--orange)"/>
    </svg>

    <h1 class="brand">Brimlow Plumbing Solutions</h1>
    <p class="tagline">Your local reliable Sydney plumber – specialists in<br>Plumbing, Drainage &amp; Gas Maintenance</p>

    <div class="offer-badge">
      <span>Mention this flyer<br>to receive</span>
      <span class="discount">15% OFF</span>
      <span>your first service!</span>
    </div>

    <h2 class="services-title">Our Services</h2>

    <div class="service" style="left:120px; top:646px;"><span class="service-icon" role="img" aria-label="Emergency plumbing icon"></span>Emergency<br>Plumbing</div>
    <div class="service" style="left:278px; top:646px;"><span class="service-icon" role="img" aria-label="Drainage maintenance icon"></span>Drainage<br>Maintenance</div>
    <div class="service" style="left:432px; top:646px;"><span class="service-icon" role="img" aria-label="Drainage maintenance icon"></span>Drainage<br>Maintenance</div>
    <div class="service" style="left:592px; top:646px;"><span class="service-icon" role="img" aria-label="Hot water systems icon"></span>Hot Water Systems</div>

    <div class="service" style="left:120px; top:792px;"><span class="service-icon" role="img" aria-label="Blocked sewer icon"></span>Blocked Sewer<br>Stormwater</div>
    <div class="service" style="left:278px; top:792px;"><span class="service-icon" role="img" aria-label="Blocked stormwater icon"></span>Blocked &amp;<br>Stormwater</div>
    <div class="service" style="left:432px; top:792px;"><span class="service-icon" role="img" aria-label="Camera and locating icon"></span>Camera &amp;<br>TMV Locating</div>
    <div class="service" style="left:592px; top:792px;"><span class="service-icon" role="img" aria-label="TMV maintenance icon"></span>TMV Maintenance</div>

    <footer class="contact-bar">
      <div class="contact-item phone">
        <svg class="contact-icon" viewBox="0 0 24 24" aria-hidden="true"><circle cx="12" cy="12" r="12" fill="var(--white)"/><path d="M8.2 6.5l2 .2.9 2.4-1.3 1c.7 1.5 1.8 2.6 3.3 3.3l1-1.3 2.4.9.2 2c-.2.7-.9 1.2-1.7 1.1C10.7 15.7 8.3 13.3 7.9 9.1c-.1-.8.4-1.5 1.1-1.7z" fill="var(--sky)" transform="translate(-1 -.5)"/></svg>
        0400 318 562
      </div>
      <div class="contact-item">
        <svg class="contact-icon" viewBox="0 0 24 24" aria-hidden="true"><circle cx="12" cy="12" r="12" fill="var(--white)"/><rect x="6" y="8" width="12" height="8.5" rx="1" fill="none" stroke="var(--sky)" stroke-width="1.5"/><path d="M6.5 8.6L12 12.8l5.5-4.2" fill="none" stroke="var(--sky)" stroke-width="1.5"/></svg>
        hello@brimlowplumbing.com.au
      </div>
      <div class="contact-item">
        <svg class="contact-icon" viewBox="0 0 24 24" aria-hidden="true"><circle cx="12" cy="12" r="12" fill="var(--white)"/><circle cx="12" cy="12" r="5" fill="var(--sky)"/></svg>
        @BrimlowPlumbing
      </div>
    </footer>
  </main>
</body>
</html>
```